New Business Cards for Tormin Group

We need a new Business Card to compliment our new logo. We are a vibrant design, manufacture and install business providing recreation areas, public parks and Municipal spaces. We want business cards that are classy, modern and clean.

We have recently changed our logo, and are celebrating our 40th anniversary. We want business cards with a new modern design to reflect our status.

Target Market(s)

Customers

Contact Information for Business Card

We need all the details of our 3 offices as per the business card attached. Please disregard the old logo on the business card, the other three files show our new logo.

Requirements
Must have
• All info as per attached business card but with new logo.
Nice to have

```html
<!DOCTYPE html>
<html lang="en">
<head>
<meta charset="utf-8">
<title>Tormin Group – Business Card</title>
<link href="https://fonts.googleapis.com/css2?family=Lato:wght@400;700&display=swap" rel="stylesheet">
<style>
  :root {
    --stage: #5e5e5e;
    --card: #ffffff;
    --red: #ee3440;
    --ink: #3a3a3c;
    --muted: #666668;
    --rule: #8a8a8a;
    --band: #4a4a4c;
    --band-text: #f2f2f2;
  }
  html, body {
    margin: 0;
    width: 1200px;
    height: 1200px;
    overflow: hidden;
    background: var(--stage);
    font-family: "Lato", sans-serif;
  }
  .card {
    position: absolute;
    left: 90px;
    top: 303px;
    width: 1020px;
    height: 593px;
    background: var(--card);
    border-radius: 32px 44px 14px 14px;
    overflow: hidden;
  }
  .brand {
    position: absolute;
    left: 39px;
    top: 72px;
    display: flex;
    align-items: center;
    gap: 18px;
  }
  .brand-dot {
    width: 120px;
    height: 120px;
    border-radius: 50%;
    background: var(--red);
  }
  .brand-name {
    font-size: 46px;
    font-weight: 700;
    color: var(--ink);
    letter-spacing: 1px;
  }
  .person {
    position: absolute;
    right: 33px;
    top: 76px;
    text-align: right;
  }
  .person-name {
    font-size: 35px;
    color: var(--red);
    line-height: 1;
  }
  .person-title {
    margin-top: 14px;
    font-size: 25px;
    color: var(--ink);
  }
  .direct {
    position: absolute;
    right: 33px;
    top: 244px;
    text-align: right;
    font-size: 19px;
    color: var(--ink);
  }
  .direct-line {
    display: flex;
    justify-content: flex-end;
    align-items: center;
    gap: 12px;
    height: 35px;
  }
  .direct-line svg { width: 13px; height: 13px; fill: var(--red); }
  .divider {
    position: absolute;
    left: 32px;
    right: 32px;
    top: 339px;
    height: 2px;
    background: var(--rule);
  }
  .office {
    position: absolute;
    top: 360px;
    text-align: right;
    color: var(--muted);
    font-size: 19.5px;
    line-height: 30.5px;
  }
  .office-title {
    font-size: 24px;
    color: var(--red);
    line-height: 1;
    margin-bottom: 14px;
  }
  .office--head { right: 685px; }
  .office--dubai { right: 348px; }
  .office--qatar { right: 32px; top: 363px; }
  .footer {
    position: absolute;
    left: 0;
    bottom: 0;
    width: 1020px;
    height: 60px;
  }
  .website {
    position: absolute;
    right: 33px;
    bottom: 17px;
    font-size: 19px;
    color: var(--band-text);
  }
</style>
</head>
<body>
  <div class="card">
    <div class="brand">
      <div class="brand-dot"></div>
      <div class="brand-name">TORMIN GROUP</div>
    </div>

    <div class="person">
      <div class="person-name">Sami Haddara</div>
      <div class="person-title">Managing Partner</div>
    </div>

    <div class="direct">
      <div class="direct-line">+971 (0)50 384 1726
        <svg viewBox="0 0 24 24"><path d="M6.6 10.8a15 15 0 0 0 6.6 6.6l2.2-2.2a1 1 0 0 1 1-.25 11.4 11.4 0 0 0 3.6.6 1 1 0 0 1 1 1V20a1 1 0 0 1-1 1A17 17 0 0 1 3 4a1 1 0 0 1 1-1h3.5a1 1 0 0 1 1 1c0 1.25.2 2.45.6 3.6a1 1 0 0 1-.25 1z"/></svg>
      </div>
      <div class="direct-line">sami@tormingroup.com
        <svg viewBox="0 0 24 24"><path d="M2 5h20v14H2z M2 5l10 8 10-8" /><path d="M3 6l9 7 9-7" fill="#fff"/></svg>
      </div>
    </div>

    <div class="divider"></div>

    <div class="office office--head">
      <div class="office-title">Head Office</div>
      <div>P.O. Box: 41803 Abu Dhabi. U.A.E</div>
      <div>Tel No: +971 (0)2 5530172</div>
      <div>Fax No: +971(0)2 5530173</div>
      <div>Email: sales@tormingroup.com</div>
    </div>

    <div class="office office--dubai">
      <div class="office-title">Dubai Office</div>
      <div>P.O. Box: 287410 Dubai, U.A.E</div>
      <div>Tel No: +971 (0)4 386205</div>
      <div>Fax No: +971(0)4 386294</div>
      <div>Email: sales@tormingroup.com</div>
    </div>

    <div class="office office--qatar">
      <div class="office-title">Qater Office</div>
      <div>P.O. Box: 30592 Doha, Qatter</div>
      <div>Tel No: +974 44718350</div>
      <div>Fax No: +971 44290517</div>
      <div>Email: sales@tormingroup.com</div>
    </div>

    <svg class="footer" viewBox="0 0 1020 60" preserveAspectRatio="none">
      <path d="M0 15 H490 Q505 15 515 8 L522 3 Q528 0 540 0 H1020 V60 H0 Z" fill="var(--band)"/>
      <path d="M0 16 H492 Q506 16 514 11 L512 24 Q505 27 492 27 H0 Z" fill="var(--red)"/>
      <rect x="0" y="27" width="1020" height="33" fill="var(--band)"/>
      <path d="M0 27 H495 Q506 27 512 24 L520 20 V27 H0 Z" fill="var(--card)" opacity="0"/>
    </svg>
    <div class="website">www.tormingroup.com</div>
  </div>
</body>
</html>
```